Construction company business card

One side to be the logo with the company name, The other side I would like: (Tomas verbick) Project manager 41 barrow crescent hallam 52917306224783(03) 9703 2428Info@gudeljgroup.comAnd then maybe a couple dot points saying what we do:Construction (commercial & industrial) Civil construction

Anything else please contact me!
Maybe curved st one edge of the card

Target Market(s)

Older clientele

Industry/Entity Type

Construction Company

Contact Information for Business Card

Read above

Colors
3277b5
1b1b1b
9d9d9d

Requirements
Must have
• Use my logo on one side
Nice to have
• Read above
Should not have
• Read above

```html
<!DOCTYPE html>
<html lang="en">
<head>
<meta charset="utf-8">
<title>Kestrel Property Group – Business Card</title>
<link href="https://fonts.googleapis.com/css2?family=Open+Sans:wght@400;600&family=Lato:wght@700&display=swap" rel="stylesheet">
<style>
  :root {
    --brand-blue: #3277b5;
    --ink: #1b1b1b;
    --grey: #9d9d9d;
    --text-grey: #555555;
    --paper: #ffffff;
    --backdrop: #3b3b3d;
  }
  * { box-sizing: border-box; margin: 0; padding: 0; }
  html, body { width: 1200px; height: 1200px; overflow: hidden; }
  body {
    background: var(--backdrop);
    font-family: "Open Sans", Arial, sans-serif;
    position: relative;
  }
  .card {
    position: absolute;
    left: 220px;
    width: 760px;
    height: 434px;
    box-shadow: 0 10px 24px rgba(0,0,0,0.35);
  }
  /* Back of card */
  .card--back {
    top: 140px;
    background: var(--brand-blue);
    border-radius: 90px 0 90px 0;
    color: var(--paper);
  }
  .back-brand {
    position: absolute;
    top: 170px;
    left: 0; right: 0;
    display: flex;
    justify-content: center;
    align-items: center;
    gap: 16px;
  }
  .back-brand__dot {
    width: 22px; height: 22px;
    border-radius: 50%;
    background: var(--paper);
  }
  .back-brand__name {
    font-family: "Lato", Arial, sans-serif;
    font-weight: 700;
    font-size: 40px;
    letter-spacing: 1px;
    color: var(--paper);
  }
  .services {
    position: absolute;
    left: 60px; right: 60px;
    bottom: 48px;
    display: flex;
    justify-content: space-between;
    font-size: 21px;
    list-style: none;
  }
  .services li::before {
    content: "";
    display: inline-block;
    width: 9px; height: 9px;
    border-radius: 50%;
    background: var(--paper);
    margin-right: 9px;
    vertical-align: middle;
  }
  /* Front of card */
  .card--front {
    top: 626px;
    background: var(--paper);
    border-radius: 0 90px 0 90px;
  }
  .front-brand {
    position: absolute;
    left: 40px;
    top: 150px;
    width: 330px;
    display: flex;
    align-items: center;
    gap: 14px;
  }
  .front-brand__dot {
    flex: none;
    width: 26px; height: 26px;
    border-radius: 50%;
    background: var(--brand-blue);
  }
  .front-brand__name {
    font-family: "Lato", Arial, sans-serif;
    font-weight: 700;
    font-size: 38px;
    line-height: 1.1;
    color: var(--brand-blue);
  }
  .divider {
    position: absolute;
    left: 392px;
    top: 60px;
    width: 1px;
    height: 300px;
    background: linear-gradient(to bottom, transparent, var(--grey), transparent);
  }
  .contact {
    position: absolute;
    left: 425px;
    top: 90px;
    color: var(--text-grey);
    font-size: 21px;
    line-height: 1.22;
  }
  .contact__name {
    font-weight: 600;
    font-size: 25px;
    color: var(--brand-blue);
    text-transform: uppercase;
  }
  .contact__role { margin-bottom: 12px; }
  .contact__address { margin-bottom: 12px; }
  .contact__line { display: flex; align-items: center; gap: 8px; }
  .contact__line svg { width: 16px; height: 16px; fill: var(--brand-blue); flex: none; }
</style>
</head>
<body>
  <section class="card card--back">
    <div class="back-brand">
      <span class="back-brand__dot"></span>
      <span class="back-brand__name">Kestrel Property Group</span>
    </div>
    <ul class="services">
      <li>Construction (commercial &amp; industrial)</li>
      <li>Civil construction</li>
    </ul>
  </section>

  <section class="card card--front">
    <div class="front-brand">
      <span class="front-brand__dot"></span>
      <span class="front-brand__name">Kestrel<br>Property Group</span>
    </div>
    <div class="divider"></div>
    <div class="contact">
      <p class="contact__name">Tomas Verbick</p>
      <p class="contact__role">Project manager</p>
      <p class="contact__address">41 barrow crescent<br>larkfield 5291</p>
      <p class="contact__line">
        <svg viewBox="0 0 16 16" aria-hidden="true"><path d="M2 6c0-2 3-3.5 6-3.5S14 4 14 6l-2.5 1-1-1.5h-5l-1 1.5z"/><rect x="4" y="8" width="8" height="6" rx="1"/></svg>
        7306224783
      </p>
      <p class="contact__line">
        <svg viewBox="0 0 16 16" aria-hidden="true"><path d="M4.5 1h7a1 1 0 0 1 1 1v12a1 1 0 0 1-1 1h-7a1 1 0 0 1-1-1V2a1 1 0 0 1 1-1zm1 2v9h5V3z"/></svg>
        (03) 9418 6573
      </p>
      <p class="contact__line">
        <svg viewBox="0 0 16 16" aria-hidden="true"><path d="M1 3h14v10H1zm1.5 1.2L8 8.5l5.5-4.3z"/></svg>
        Info@verbickgroup.com
      </p>
    </div>
  </section>
</body>
</html>
```